Velk Partners Building Business Cards

We need a business card that reflects our business as "Solar Experts" in San Diego. Browse our website www.velkpartners.example our License needs to be displayed as "CSLB# 3867140" our phone number is (619) 555-0187

Save thousands on your electric bills and increase the value of your home while helping to protect the environment. Our solar installation experts will help you design the system that's right for you, using only the highest quality equipment that will look great and give you ideal performance. Our goal is to make you energy independent, and get your electric bill to 0.

Paul Osterby
(619) 555-0187
paul@velkpartners.example

Target Market(s)

Home owners in san diego looking for solar

Industry/Entity Type

Solar Energy

Contact Information for Business Card

Paul Osterby
(619) 555-0187
paul@velkpartners.example

Font styles to use
Other font styles liked:
• Use our logo font

Requirements
Must have
• License needs to be displayed as "CSLB# 3867140" our phone number is (619) 555-0187
Nice to have
• Real images of rooftop home solar in san diego
Should not have
• our business address

```html
<!DOCTYPE html>
<html lang="en">
<head>
<meta charset="utf-8">
<title>Velk Partners Building – Business Card</title>
<link href="https://fonts.googleapis.com/css2?family=Roboto:wght@400;500;700&display=swap" rel="stylesheet">
<style>
  :root{
    --bg:#a9a7a8;
    --navy:#25447f;
    --navy-deep:#1f3a73;
    --navy-light:#3a5c9c;
    --navy-text:#1e3b78;
    --gold:#eea915;
    --paper:#fbfbfa;
    --white:#ffffff;
  }
  *{margin:0;padding:0;box-sizing:border-box}
  html,body{width:1200px;height:1200px;overflow:hidden}
  body{background:var(--bg);font-family:"Roboto",Arial,sans-serif;position:relative}

  .card{position:absolute;width:712px;height:418px;border-radius:24px;overflow:hidden}

  /* Front */
  .card-front{left:238px;top:118px;background:var(--navy)}
  .front-photo{position:absolute;inset:0;
    background:
      radial-gradient(ellipse 60% 45% at 12% 8%, rgba(90,120,175,.55) 0%, rgba(90,120,175,0) 100%),
      radial-gradient(ellipse 55% 60% at 85% 80%, rgba(20,45,95,.55) 0%, rgba(20,45,95,0) 100%),
      radial-gradient(ellipse 70% 40% at 60% 35%, rgba(60,95,160,.35) 0%, rgba(60,95,160,0) 100%),
      linear-gradient(160deg,#34569a 0%,var(--navy) 45%,var(--navy-deep) 100%)}
  .front-name{position:absolute;left:0;right:0;top:160px;text-align:center;
    color:var(--white);font-weight:700;font-size:52px;letter-spacing:-1px;line-height:1}
  .front-license{position:absolute;left:0;right:0;top:364px;display:flex;
    justify-content:center;align-items:center;gap:20px;color:var(--white);font-size:17px}
  .front-license .rule{width:55px;height:3px;background:var(--gold)}

  /* Back */
  .card-back{left:231px;top:644px;background:var(--paper)}
  .back-band{position:absolute;left:0;top:0}
  .back-brand{position:absolute;left:20px;top:118px;width:290px;display:flex;
    flex-direction:column;align-items:center;gap:18px}
  .back-brand .dot{width:86px;height:86px;border-radius:50%;background:var(--gold)}
  .back-brand p{color:var(--white);font-weight:700;font-size:30px;line-height:1.1;
    text-align:center;letter-spacing:-.5px}
  .contact{position:absolute;left:396px;top:116px;color:var(--navy-text)}
  .contact-name{font-size:24px;font-weight:700;line-height:1.1}
  .contact-title{font-size:16px;margin-top:6px}
  .contact-list{list-style:none;margin-top:30px}
  .contact-list li{display:flex;align-items:center;gap:16px;font-size:18px;height:25px}
  .contact-list svg{width:20px;height:16px;flex:none}
  .accent{color:var(--gold)}
  .contact-license{font-size:18px;margin-top:8px}
</style>
</head>
<body>

  <section class="card card-front">
    <div class="front-photo" role="img" aria-label="Rooftop solar panels photo, tinted blue"></div>
    <h1 class="front-name">Velk Partners Building</h1>
    <p class="front-license"><span class="rule"></span>License: CSLB# 3867140<span class="rule"></span></p>
  </section>

  <section class="card card-back">
    <svg class="back-band" width="712" height="418" viewBox="0 0 712 418">
      <path d="M0,0 H327 C360,100 372,210 350,305 C340,350 320,390 302,418 H0 Z" fill="var(--gold)"/>
      <path d="M0,0 H319 C352,100 364,210 342,305 C332,350 312,390 294,418 H0 Z" fill="var(--navy)"/>
    </svg>

    <div class="back-brand">
      <span class="dot"></span>
      <p>Velk Partners<br>Building</p>
    </div>

    <div class="contact">
      <p class="contact-name">Paul Osterby</p>
      <p class="contact-title">Managing Director</p>
      <ul class="contact-list">
        <li>
          <svg viewBox="0 0 20 16"><path d="M2 5 C4 1 16 1 18 5 L15 7 L13 5 H7 L5 7 Z M5 8 H15 L17 15 H3 Z" fill="var(--gold)"/></svg>
          (619) 555-0187
        </li>
        <li>
          <svg viewBox="0 0 20 16"><circle cx="10" cy="8" r="7" fill="none" stroke="var(--gold)" stroke-width="1.6"/><ellipse cx="10" cy="8" rx="3" ry="7" fill="none" stroke="var(--gold)" stroke-width="1.4"/><path d="M3 8 H17" stroke="var(--gold)" stroke-width="1.4"/></svg>
          paul@velkpartners.example
        </li>
        <li>
          <svg viewBox="0 0 20 16"><rect x="1" y="2" width="18" height="12" fill="var(--gold)"/><path d="M1 2 L10 9 L19 2" fill="none" stroke="var(--paper)" stroke-width="1.5"/></svg>
          <span>www.<span class="accent">velkpartners</span>.example</span>
        </li>
      </ul>
      <p class="contact-license">License: CSLB# 3867140</p>
    </div>
  </section>

</body>
</html>
```